Corvane Business Cards

Front of business card will have logo, name, address, & telephone number. Back of card will have a list of services provided - Roads, Substation Pads, Temporary Pads, Site Pads, Land Leveling, Powerline Row Cleaning, Land Clearing, Gates, Fencing, Construction Entrances, Excavation, Trenching, Underground Utilities, Directional Boring, Pile Driving. We are a construction company that uses heavy equipment like bulldozers, motor graders/blades, dump trucks, backhoes, hydro axes, & skid loaders. We build roads, pads, & install electric utility lines & waterlines underground. This logo is new. The word "Construction" can be smaller as uploaded 2 example edited logos. We will be using this card design for many employees.
Target Market(s)
Industrial Electric Powerline, Wind Turbine, Solar Panel, & Water Utility companies.
Contact Information for Business Card
Name/Position - Dwayne Halster - Owner
Address: 4875 FM 309
Merkel, TX 79412
Phone number - (325) 482-5096

```html
<!DOCTYPE html>
<html lang="en">
<head>
<meta charset="UTF-8">
<title>Corvane Construction – Business Cards</title>
<link href="https://fonts.googleapis.com/css2?family=Montserrat:wght@400;600;700&family=Roboto:wght@400;700&display=swap" rel="stylesheet">
<style>
  :root {
    --page-bg: #d9d6d4;
    --card-maroon: #3d111c;
    --card-maroon-light: #4a1a25;
    --ink-light: #ffffff;
    --ink-soft: rgba(255, 255, 255, 0.92);
  }
  * { box-sizing: border-box; margin: 0; padding: 0; }
  html, body {
    width: 1200px;
    height: 900px;
    overflow: hidden;
    background: var(--page-bg);
  }
  .canvas {
    width: 1200px;
    height: 900px;
    display: flex;
    flex-direction: column;
    align-items: center;
    justify-content: center;
    gap: 36px;
  }
  .card {
    width: 700px;
    height: 400px;
    background: linear-gradient(120deg, var(--card-maroon-light) 0%, var(--card-maroon) 35%, var(--card-maroon) 100%);
    color: var(--ink-light);
    position: relative;
    overflow: hidden;
    box-shadow: 0 10px 24px rgba(0, 0, 0, 0.25);
  }

  /* Services side */
  .card--services {
    display: flex;
    flex-direction: column;
    align-items: center;
    justify-content: center;
    gap: 58px;
  }
  .wordmark {
    display: flex;
    align-items: center;
    gap: 14px;
    font-family: "Montserrat", sans-serif;
    font-weight: 700;
    color: var(--ink-light);
    letter-spacing: 0.04em;
    white-space: nowrap;
  }
  .wordmark__mark {
    background: var(--ink-light);
    flex: none;
  }
  .wordmark--large { font-size: 58px; }
  .wordmark--large .wordmark__mark { width: 34px; height: 34px; }
  .services {
    font-family: "Montserrat", sans-serif;
    font-weight: 400;
    font-size: 15.5px;
    line-height: 1.55;
    text-align: center;
    color: var(--ink-soft);
    letter-spacing: 0.01em;
  }
  .services .sep { margin: 0 6px; }

  /* Contact side */
  .card--contact {
    display: flex;
    align-items: center;
    padding: 0 30px 0 56px;
  }
  .brand-block {
    width: 250px;
    flex: none;
    display: flex;
    flex-direction: column;
    align-items: flex-start;
    gap: 6px;
    margin-top: 80px;
  }
  .wordmark--small { font-size: 38px; gap: 10px; }
  .wordmark--small .wordmark__mark { width: 22px; height: 22px; }
  .brand-block__tagline {
    font-family: "Montserrat", sans-serif;
    font-weight: 700;
    font-size: 23px;
    letter-spacing: 0.06em;
    color: var(--ink-light);
    white-space: nowrap;
  }
  .divider {
    flex: none;
    width: 1px;
    height: 150px;
    background: var(--ink-soft);
    margin: 40px 28px 0 14px;
  }
  .contact {
    flex: 1;
    min-width: 0;
    font-family: "Roboto", sans-serif;
    color: var(--ink-light);
    margin-top: -20px;
  }
  .contact__name {
    font-weight: 700;
    font-size: 23px;
    letter-spacing: 0.02em;
    text-transform: uppercase;
    white-space: nowrap;
  }
  .contact__role {
    font-size: 17px;
    margin-top: 2px;
    margin-left: 16px;
  }
  .contact__list {
    list-style: none;
    margin-top: 20px;
    margin-left: 22px;
    font-size: 17px;
    line-height: 1.65;
  }
  .contact__item {
    display: flex;
    align-items: center;
    gap: 8px;
    white-space: nowrap;
  }
  .contact__icon { width: 13px; height: 13px; flex: none; }
</style>
</head>
<body>
<main class="canvas">

  <section class="card card--services" aria-label="Services side">
    <div class="wordmark wordmark--large">
      <span class="wordmark__mark" aria-hidden="true"></span>
      <span class="wordmark__name">CORVANE</span>
    </div>
    <p class="services">
      Roads<span class="sep">I</span>Substation Pads<span class="sep">I</span>Temporary Pads<span class="sep">I</span>Site Pads<span class="sep">I</span>Land Leveling<br>
      Land Clearing<span class="sep">I</span>Gates<span class="sep">I</span>Fencing<span class="sep">I</span>Construction Entrances<span class="sep">I</span>Excavation<span class="sep">I</span>Trenching<br>
      Underground Utilities<span class="sep">I</span>Powerline Row Cleaning<span class="sep">I</span>Pile Driving<span class="sep">I</span>Directional Boring
    </p>
  </section>

  <section class="card card--contact" aria-label="Contact side">
    <div class="brand-block">
      <div class="wordmark wordmark--small">
        <span class="wordmark__mark" aria-hidden="true"></span>
        <span class="wordmark__name">CORVANE</span>
      </div>
      <div class="brand-block__tagline">CONSTRUCTION</div>
    </div>
    <div class="divider" aria-hidden="true"></div>
    <div class="contact">
      <div class="contact__name">Dwayne Halster</div>
      <div class="contact__role">Owner</div>
      <ul class="contact__list">
        <li class="contact__item">
          <svg class="contact__icon" viewBox="0 0 24 24" aria-hidden="true">
            <path fill="#ffffff" d="M6.6 10.8a15.1 15.1 0 0 0 6.6 6.6l2.2-2.2a1 1 0 0 1 1-.25 11.4 11.4 0 0 0 3.6.57 1 1 0 0 1 1 1V20a1 1 0 0 1-1 1A17 17 0 0 1 3 4a1 1 0 0 1 1-1h3.5a1 1 0 0 1 1 1c0 1.250.2 2.450.57 3.570a1 1 0 0 1-.25 1z"/>
          </svg>
          (325) 482-5096
        </li>
        <li class="contact__item">
          <svg class="contact__icon" viewBox="0 0 24 24" aria-hidden="true">
            <path fill="#ffffff" d="M12 2a7 7 0 0 0-7 7c0 5.25 7 13 7 13s7-7.75 7-13a7 7 0 0 0-7-7zm0 9.5A2.5 2.5 0 1 1 12 6.5a2.5 2.5 0 0 1 0 5z"/>
          </svg>
          4875 FM 309 Merkel, TX 79412
        </li>
      </ul>
    </div>
  </section>

</main>
</body>
</html>
```